Shopping centre customer engagement software website

We need a multi page site with :

*What we do.
*How it works.
*Benefits
* Case study
* Testimonial
* Business login (we provide link to business portal)
* Consumer login (we provide link to consumer site)
* Book a demo
* Contact us

We want it to be clean and crisp and very self explanatory with little clutter. We are thinking white but are open to what ever looks the best.
Updates

Wordpress is preferred

Need extra days to review

Target Market(s)

Shopping centre managers and retail property companies

Coding

Coded - Design and coding required

Number of Pages Required

5+ page

Font styles to use
Sans Serif

Colors
ffffff

Requirements
Must have
• As listed above and must be responsive! Checkout our existing site for the text to be included (will be edited but it’ll give you an idea) www.vostrelink.com

```html
<!DOCTYPE html>
<html lang="en">
<head>
<meta charset="utf-8">
<title>Vostrelink – Shopping Centre Customer Engagement</title>
<link href="https://fonts.googleapis.com/css2?family=Raleway:wght@300;400;600;700&family=Lato:wght@300;400;700&display=swap" rel="stylesheet">
<style>
:root{
  --teal:#3f9aa3;
  --teal-dark:#2f7a82;
  --ink:#2e2e2e;
  --text:#555a5e;
  --muted:#7b7f82;
  --page:#d9d9d9;
  --band:#cfcfcf;
  --panel:#c9c9c9;
  --hero-top:#3c3f42;
  --hero-bot:#6a6d70;
  --dark-band:#3a3a3c;
  --footer:#d2d2d2;
  --copy:#c4c4c4;
  --white:#f4f4f4;
}
*{margin:0;padding:0;box-sizing:border-box}
html,body{width:1200px;height:3612px;overflow:hidden}
body{background:var(--page);font-family:'Lato',sans-serif;color:var(--text);position:relative}
h2{font-family:'Raleway',sans-serif;font-weight:600;color:var(--ink);letter-spacing:2px;font-size:30px}
p{font-size:15px;line-height:1.75}
.btn{display:inline-block;font-family:'Raleway',sans-serif;font-size:12px;font-weight:600;letter-spacing:1px;color:var(--white);background:var(--teal);border-radius:20px;padding:9px 24px}
.photo{position:absolute}

/* header */
.site-header{position:absolute;left:0;top:0;width:1200px;height:110px;z-index:3}
.brand{position:absolute;left:28px;top:16px;display:flex;align-items:center;gap:10px}
.brand-dot{width:64px;height:64px;border-radius:50%;background:#e0e0e0}
.brand-name{font-family:'Raleway',sans-serif;font-weight:600;font-size:14px;color:#e8e8e8;letter-spacing:2px}
.nav{position:absolute;left:280px;top:46px;display:flex;gap:40px;font-family:'Raleway',sans-serif;font-size:13px;font-weight:600;color:#e6e6e6;letter-spacing:1px}
.login{position:absolute;top:36px;font-family:'Raleway',sans-serif;font-size:12px;font-weight:600;letter-spacing:1px;border-radius:20px;padding:9px 18px}
.login-business{left:800px;background:var(--teal);color:var(--white)}
.login-consumer{left:955px;border:2px solid var(--teal);color:var(--teal)}

/* hero */
.hero{position:absolute;left:0;top:0;width:1200px;height:760px;background:linear-gradient(180deg,var(--hero-top),var(--hero-bot));overflow:hidden}
.hero-title{position:absolute;left:40px;top:140px;font-family:'Raleway',sans-serif;font-weight:300;font-size:72px;line-height:1;letter-spacing:10px;color:rgba(230,230,230,.6);z-index:2}
.hero-sub{position:absolute;left:42px;top:232px;font-family:'Raleway',sans-serif;font-size:20px;color:#e2e2e2;line-height:1.35;z-index:2}
.hero-video{position:absolute;left:272px;top:304px;width:656px;height:416px;border:4px solid #f0f0f0;background:linear-gradient(135deg,#5b6670,#8d8a84 55%,#4e5a66);z-index:2}
.play{position:absolute;left:290px;top:170px}
.hero-curve{position:absolute;left:0;top:640px;z-index:1}

/* welcome */
.monitor{position:absolute;left:100px;top:820px;width:420px;height:340px;background:linear-gradient(180deg,#4a4c4f,#8a8c8e 70%,#b8b8b8)}
.welcome-copy{position:absolute;left:600px;top:848px;width:520px}
.welcome-copy p{margin:20px 0 18px}

/* what we do */
.what{position:absolute;left:0;top:1236px;width:1200px;height:500px;background:var(--band)}
.what-copy{position:absolute;left:40px;top:60px;width:500px}
.what-copy p{margin-top:22px}
.what-copy .btn{margin-top:22px}

/* benefits */
.benefits{position:absolute;left:0;top:1736px;width:1200px;height:480px;background:var(--panel)}
.benefits-copy{position:absolute;left:660px;top:70px;width:480px}
.benefits-copy p{margin-top:18px;font-size:13px}
.benefit-list{position:absolute;left:640px;top:234px;width:500px;display:flex;justify-content:space-around;text-align:center}
.benefit{width:140px;font-size:12px;line-height:1.4;color:var(--text)}
.benefit svg{display:block;margin:0 auto 10px}
.benefits .btn{position:absolute;left:822px;top:394px;padding:6px 18px;font-size:11px}
.arrow{position:absolute}

/* how it works */
.how{position:absolute;left:0;top:2300px;width:1200px;text-align:center}
.how p{width:560px;margin:14px auto 0;font-size:13px}
.steps{position:absolute;left:80px;top:180px;width:1040px;display:flex;justify-content:space-between}
.step{width:150px;text-align:center;font-family:'Raleway',sans-serif;font-weight:600;font-size:14px;color:var(--ink)}
.step svg{display:block;margin:0 auto 18px}
.step-link{position:absolute;top:220px}

/* case study */
.cases{position:absolute;left:0;top:2740px;width:1200px;height:500px;background:var(--dark-band)}
.cases h2{position:absolute;left:0;width:1200px;top:70px;text-align:center;color:#ececec}
.case-card{position:absolute;left:140px;top:160px;width:360px;height:300px;background:#ececec}
.case-label{position:absolute;left:18px;bottom:14px;font-family:'Raleway',sans-serif;font-weight:700;font-size:13px;color:var(--ink);letter-spacing:1px}
.case-label span{font-weight:400;color:var(--muted);margin-left:16px}
.quote{position:absolute;left:600px;top:166px;width:520px;color:#d8d8d8}
.quote p{font-style:italic;font-size:14px}
.quote-name{margin-top:18px;font-family:'Raleway',sans-serif;font-weight:600;color:#eee;font-size:14px}
.quote-role{font-size:13px;color:#bbb;margin-top:6px}

/* contact */
.contact{position:absolute;left:0;top:3240px;width:1200px;height:300px;background:var(--footer)}
.contact h3{position:absolute;left:100px;top:110px;font-family:'Raleway',sans-serif;font-weight:700;font-size:17px;color:var(--ink);letter-spacing:1px}
.contact-cols{position:absolute;left:100px;top:160px;width:840px;display:flex;justify-content:space-between}
.contact-col{font-size:11px;line-height:2.1;color:var(--text)}
.contact-col div{display:flex;align-items:center;gap:8px}
.social{position:absolute;left:960px;top:162px;display:flex;gap:10px}
.social span{width:26px;height:26px;border-radius:50%;border:1px solid var(--muted);display:block}
.copyright{position:absolute;left:0;top:3540px;width:1200px;height:72px;background:var(--copy);text-align:center;line-height:72px;font-size:12px;color:var(--muted)}
</style>
</head>
<body>

<section class="hero">
  <div class="photo" role="img" aria-label="Office interior photograph behind the hero" style="inset:0;background:linear-gradient(100deg,#34383c,#5c6064 45%,#3f4347)"></div>
  <div class="hero-title">VOSTRELINK</div>
  <div class="hero-sub">People exceed expectations<br>Managers Shopping centres</div>
  <div class="hero-video" role="img" aria-label="Video still of a man in a blue shirt using a tablet">
    <svg class="play" width="70" height="70" viewBox="0 0 70 70"><circle cx="35" cy="35" r="32" fill="#f2f2f2" stroke="#222" stroke-width="3"/><path d="M28 22 L50 35 L28 48 Z" fill="#222"/></svg>
  </div>
  <svg class="hero-curve" width="1200" height="120" viewBox="0 0 1200 120"><path d="M0 80 Q600 -10 1200 80 L1200 120 L0 120 Z" fill="var(--page)"/></svg>
</section>

<header class="site-header">
  <div class="brand"><span class="brand-dot"></span></div>
  <div class="brand" style="left:30px;top:88px"><span class="brand-name">VOSTRELINK</span></div>
  <nav class="nav"><span>WHAT WE DO</span><span>BENEFITS</span><span>HOW IT WORKS</span><span>CASE STUDY</span></nav>
  <span class="login login-business">BUSINESS LOGIN</span>
  <span class="login login-consumer">CONSUMER LOGIN</span>
</header>

<section class="welcome">
  <div class="monitor" role="img" aria-label="Desktop monitor mockup showing the analytics dashboard"></div>
  <div class="welcome-copy">
    <h2>WELCOME TO VOSTRELINK</h2>
    <p>Vostrelink gives shopping centre managers a simple way to reach every shopper in the mall. Our platform links visitors, retailers and centre teams through one clear app, rewarding loyalty and turning every visit into useful insight for your property.</p>
    <span class="btn">READ MORE</span>
  </div>
</section>

<section class="what">
  <div class="what-copy">
    <h2>WHAT WE DO</h2>
    <p>We help centre managers connect with shoppers in real time, send targeted offers from their own stores and reward repeat visits. Every interaction is captured so your team can see what works and plan better campaigns.</p>
    <p>Retailers gain a direct channel to nearby customers, while shoppers enjoy deals that matter to them. The result is a livelier centre, stronger tenant relationships and clear data behind each decision you make.</p>
    <span class="btn">READ MORE</span>
  </div>
  <div class="photo" role="img" aria-label="Photograph of a team working at computer screens" style="left:600px;top:0;width:600px;height:500px;background:linear-gradient(135deg,#5a646c,#8c949a 55%,#5e6468)"></div>
</section>

<section class="benefits">
  <div class="photo" role="img" aria-label="Photograph of a smiling man working at a laptop" style="left:0;top:0;width:600px;height:480px;background:linear-gradient(135deg,#b8bcbf,#8d99a3 55%,#c9c9c9)"></div>
  <svg class="arrow" style="left:618px;top:240px" width="16" height="28" viewBox="0 0 16 28"><path d="M13 2 L3 14 L13 26" stroke="var(--muted)" stroke-width="3" fill="none"/></svg>
  <svg class="arrow" style="left:1166px;top:240px" width="16" height="28" viewBox="0 0 16 28"><path d="M3 2 L13 14 L3 26" stroke="var(--muted)" stroke-width="3" fill="none"/></svg>
  <div class="benefits-copy">
    <h2>BENEFITS</h2>
    <p>Give your centre a clear edge: more foot traffic, happier tenants and measurable results from every campaign.</p>
  </div>
  <div class="benefit-list">
    <div class="benefit"><svg width="64" height="64" viewBox="0 0 64 64"><circle cx="32" cy="32" r="30" fill="#dde9ea" stroke="var(--teal)" stroke-width="3"/><rect x="18" y="20" width="28" height="20" rx="2" fill="#3e5d9a"/><rect x="26" y="42" width="12" height="4" fill="#3e5d9a"/></svg>Direct access to every shopper</div>
    <div class="benefit"><svg width="64" height="64" viewBox="0 0 64 64"><circle cx="32" cy="32" r="30" fill="#e9dcdc" stroke="#c35656" stroke-width="3"/><circle cx="32" cy="32" r="13" fill="none" stroke="#c35656" stroke-width="4"/><circle cx="32" cy="32" r="4" fill="#c35656"/></svg>Easy to set targeted campaigns</div>
    <div class="benefit"><svg width="64" height="64" viewBox="0 0 64 64"><circle cx="32" cy="32" r="30" fill="#dde9ea" stroke="var(--teal)" stroke-width="3"/><circle cx="32" cy="32" r="14" fill="none" stroke="var(--teal)" stroke-width="4"/><path d="M25 32 L30 37 L40 27" stroke="var(--teal)" stroke-width="4" fill="none"/></svg>Real-time data to grow the centre</div>
  </div>
  <span class="btn">Read More</span>
</section>

<section class="how">
  <h2>HOW IT WORKS</h2>
  <p>Five simple stages take a shopper from first visit to loyal customer, with clear reports for your team at each step.</p>
  <div class="steps">
    <div class="step"><svg width="80" height="80" viewBox="0 0 80 80"><rect x="14" y="22" width="44" height="30" rx="3" fill="#d9a43a"/><rect x="22" y="30" width="44" height="30" rx="3" fill="#e8c25a"/><rect x="22" y="36" width="44" height="6" fill="#3e5d9a"/></svg>Allocate Cards</div>
    <div class="step"><svg width="80" height="80" viewBox="0 0 80 80"><path d="M20 32 L48 20 L48 58 L20 46 Z" fill="#3e5d9a"/><rect x="12" y="32" width="10" height="14" fill="#c35656"/><path d="M54 30 Q62 39 54 48" stroke="#c35656" stroke-width="3" fill="none"/></svg>Direct Marketing</div>
    <div class="step"><svg width="80" height="80" viewBox="0 0 80 80"><circle cx="40" cy="34" r="18" fill="#2f4f7a"/><circle cx="40" cy="34" r="9" fill="#e8c25a"/><path d="M30 50 L26 66 L34 62 L38 68 L40 52 Z M50 50 L54 66 L46 62 L42 68 L40 52 Z" fill="#c35656"/></svg>Rewarding Loyalty</div>
    <div class="step"><svg width="80" height="80" viewBox="0 0 80 80"><path d="M14 24 L34 24 L38 30 L66 30 L66 60 L14 60 Z" fill="#d9a43a"/><rect x="18" y="36" width="44" height="20" fill="#e8c25a"/><rect x="30" y="42" width="20" height="8" fill="#3e5d9a"/></svg>Collect Data</div>
    <div class="step"><svg width="80" height="80" viewBox="0 0 80 80"><circle cx="36" cy="36" r="16" fill="none" stroke="#3e5d9a" stroke-width="5"/><path d="M48 48 L62 62" stroke="#3e5d9a" stroke-width="7" stroke-linecap="round"/><rect x="30" y="34" width="4" height="8" fill="#c35656"/><rect x="37" y="29" width="4" height="13" fill="var(--teal)"/></svg>Data Analysis</div>
  </div>
  <svg class="step-link" style="left:250px" width="90" height="24" viewBox="0 0 90 24"><path d="M4 16 Q45 0 80 12" stroke="var(--teal)" stroke-width="4" fill="none"/><path d="M74 4 L84 13 L72 18" fill="var(--teal)"/></svg>
  <svg class="step-link" style="left:472px" width="90" height="24" viewBox="0 0 90 24"><path d="M4 16 Q45 0 80 12" stroke="var(--teal)" stroke-width="4" fill="none"/><path d="M74 4 L84 13 L72 18" fill="var(--teal)"/></svg>
  <svg class="step-link" style="left:694px" width="90" height="24" viewBox="0 0 90 24"><path d="M4 16 Q45 0 80 12" stroke="var(--teal)" stroke-width="4" fill="none"/><path d="M74 4 L84 13 L72 18" fill="var(--teal)"/></svg>
  <svg class="step-link" style="left:916px" width="90" height="24" viewBox="0 0 90 24"><path d="M4 16 Q45 0 80 12" stroke="var(--teal)" stroke-width="4" fill="none"/><path d="M74 4 L84 13 L72 18" fill="var(--teal)"/></svg>
</section>

<section class="cases">
  <div class="photo" role="img" aria-label="Blurred photograph of a busy shopping centre" style="inset:0;background:linear-gradient(90deg,#3d3b3e,#56504e 50%,#3a3c40)"></div>
  <h2>CASE STUDY &amp; TESTIMONIAL</h2>
  <svg class="arrow" style="left:20px;top:236px" width="16" height="28" viewBox="0 0 16 28"><path d="M13 2 L3 14 L13 26" stroke="#e6e6e6" stroke-width="3" fill="none"/></svg>
  <svg class="arrow" style="left:1164px;top:236px" width="16" height="28" viewBox="0 0 16 28"><path d="M3 2 L13 14 L3 26" stroke="#e6e6e6" stroke-width="3" fill="none"/></svg>
  <div class="case-card">
    <div class="photo" role="img" aria-label="Photograph of a hand holding a phone showing a new message" style="left:0;top:0;width:360px;height:248px;background:linear-gradient(135deg,#6d6a66,#a29c95 55%,#5f5b57)"></div>
    <div class="case-label">MESSAGE SENT<span>VIEW</span></div>
  </div>
  <div class="quote">
    <p>“Since we started using Vostrelink our centre has seen more repeat visits and far better engagement with every campaign. Tenants now ask to join our offers, and the data helps us plan events that shoppers actually enjoy. It has become part of how we run the centre each week.”</p>
    <div class="quote-name">Sophie Marlow</div>
    <div class="quote-role">Centre Manager</div>
  </div>
</section>

<section class="contact">
  <h3>CONTACT US</h3>
  <div class="contact-cols">
    <div class="contact-col">
      <div><svg width="10" height="12" viewBox="0 0 10 12"><path d="M5 0 A4 4 0 0 1 9 4 C9 7 5 12 5 12 C5 12 1 7 1 4 A4 4 0 0 1 5 0 Z" fill="var(--muted)"/></svg>12 Harbour Street</div>
      <div><svg width="10" height="10" viewBox="0 0 10 10"><rect width="10" height="10" fill="var(--muted)"/></svg>Sydney NSW 2000</div>
      <div><svg width="10" height="8" viewBox="0 0 10 8"><rect width="10" height="8" fill="none" stroke="var(--muted)"/><path d="M0 0 L5 4 L10 0" stroke="var(--muted)" fill="none"/></svg>hello@vostrelink.com</div>
    </div>
    <div class="contact-col">
      <div><svg width="10" height="12" viewBox="0 0 10 12"><path d="M5 0 A4 4 0 0 1 9 4 C9 7 5 12 5 12 C5 12 1 7 1 4 A4 4 0 0 1 5 0 Z" fill="var(--muted)"/></svg>Level 4, 88 Quay Road</div>
      <div><svg width="10" height="10" viewBox="0 0 10 10"><rect width="10" height="10" fill="var(--muted)"/></svg>London EC1 4RT</div>
      <div><svg width="10" height="8" viewBox="0 0 10 8"><rect width="10" height="8" fill="none" stroke="var(--muted)"/><path d="M0 0 L5 4 L10 0" stroke="var(--muted)" fill="none"/></svg>uk@vostrelink.com</div>
    </div>
    <div class="contact-col">
      <div><svg width="10" height="12" viewBox="0 0 10 12"><path d="M5 0 A4 4 0 0 1 9 4 C9 7 5 12 5 12 C5 12 1 7 1 4 A4 4 0 0 1 5 0 Z" fill="var(--muted)"/></svg>5 Marlow Lane</div>
      <div><svg width="10" height="10" viewBox="0 0 10 10"><rect width="10" height="10" fill="var(--muted)"/></svg>Auckland 1010</div>
      <div><svg width="10" height="8" viewBox="0 0 10 8"><rect width="10" height="8" fill="none" stroke="var(--muted)"/><path d="M0 0 L5 4 L10 0" stroke="var(--muted)" fill="none"/></svg>nz@vostrelink.com</div>
    </div>
    <div class="contact-col">
      <div><svg width="10" height="12" viewBox="0 0 10 12"><path d="M2 0 L4 0 L5 3 L3 4 Q4 7 7 8 L8 6 L10 7 L10 10 Q4 11 1 4 Z" fill="var(--muted)"/></svg>Phone: +61 2 5550 1234</div>
      <div><svg width="10" height="8" viewBox="0 0 10 8"><rect width="10" height="8" fill="none" stroke="var(--muted)"/><path d="M0 0 L5 4 L10 0" stroke="var(--muted)" fill="none"/></svg>Email: info@vostrelink.com</div>
    </div>
  </div>
  <div class="social"><span></span><span></span><span></span></div>
</section>

<footer class="copyright">Copyright © Vostrelink Pty Ltd. All Rights Reserved.</footer>

</body>
</html>
```